limo company looking for a graphic business card with professional look and feel

Looking for a business card design that can give you the full picture of the limo company by looking at the card - we provide airport service, wedding, birthday, night out, etc... we have sedans, suvs , limos, and party buses. I want the business card to have a professional look because we are targetting corporate clients as well as regular retail.
Info about the business can be found at: http://brevlink.example/Qm4Tz7
Target Market(s)
corporate clients and retail
Industry/Entity Type
Business
Contact Information for Business Card
I would like the logo and the name of the company to be in raised print - not sure if design makes a difference for that or just print - I need it designed in 350dpi
Requirements
Must have
- pictures of vehicle types (sedans, suvs, limos, party bus). pictures of interior of the limos if possible. list service types (weddings, birthdays, proms, airport transportation) & service areas (houston, the woodlands, spring, tomball, cypress, kingwood).
Nice to have
- nice professional look to it.

```html
<!DOCTYPE html>
<html lang="en">
<head>
<meta charset="utf-8">
<title>Grandline Limousine – Business Card</title>
<link rel="stylesheet" href="https://fonts.googleapis.com/css2?family=Arimo:wght@400;700&family=Open+Sans:wght@400;600&display=swap">
<style>
  :root {
    --page: #e9e6e1;
    --card: #050505;
    --ink: #ffffff;
    --ink-soft: #d9d9d9;
    --rule: #4a4a4a;
    --shadow: rgba(0,0,0,.28);
  }
  * { box-sizing: border-box; margin: 0; padding: 0; }
  html, body { width: 1200px; height: 780px; overflow: hidden; }
  body {
    background: var(--page);
    display: flex; align-items: center; justify-content: center; gap: 30px;
    font-family: "Open Sans", Arial, sans-serif;
    color: var(--ink);
  }
  .card {
    width: 560px; height: 320px;
    background: var(--card);
    box-shadow: 0 10px 28px var(--shadow);
    position: relative; overflow: hidden;
  }

  /* ---------- front ---------- */
  .front { display: flex; }
  .front-info {
    width: 300px; padding: 34px 30px;
    display: flex; flex-direction: column; justify-content: space-between;
  }
  .person-name { font-family: Arimo, Arial, sans-serif; font-size: 26px; font-weight: 700; line-height: 1.05; }
  .person-role { font-family: Arimo, Arial, sans-serif; font-size: 15px; color: var(--ink-soft); margin-top: 2px; }
  .contact-list { list-style: none; margin-top: 14px; font-family: Arimo, Arial, sans-serif; font-size: 15px; }
  .contact-list li { display: flex; align-items: center; gap: 8px; margin-top: 5px; }
  .contact-icon { width: 16px; height: 16px; background: var(--ink); border-radius: 2px; display: flex; align-items: center; justify-content: center; }
  .brand-name { font-size: 22px; font-weight: 600; line-height: 1.2; color: var(--ink); }

  .photo-grid {
    flex: 1; display: grid;
    grid-template-columns: 1fr 1fr; grid-template-rows: 1fr 1fr;
  }
  .photo-limo-exterior { background: linear-gradient(135deg, #cfd3cf, #2a2a2a 55%, #6b7d5a); }
  .photo-limo-interior { background: radial-gradient(circle at 60% 45%, #6a6cf0, #1b1d3a 45%, #07070c); }
  .photo-party-interior { background: linear-gradient(160deg, #120810, #b0306e 55%, #3a0d22); }
  .photo-pink-limo { background: linear-gradient(150deg, #1a1a1a, #f0c3d6 55%, #b7a3a9); }
  .photo-suv { grid-column: 1 / 3; background: linear-gradient(120deg, #7a7469, #dedede 50%, #454a3f); }

  /* ---------- back ---------- */
  .back { padding: 30px 36px; }
  .back-vehicle {
    position: absolute; inset: 60px 20px 30px 20px;
    background: radial-gradient(ellipse at 50% 55%, #262626, #0b0b0b 70%, transparent);
  }
  .back-content { position: relative; }
  .back .brand-name { font-size: 24px; text-align: right; margin-bottom: 20px; }
  .info-block { padding: 9px 0; border-bottom: 1px solid var(--rule); }
  .info-block:last-child { border-bottom: none; }
  .info-title { font-family: Arimo, Arial, sans-serif; font-weight: 700; font-size: 16px; letter-spacing: .5px; }
  .info-list { font-size: 14.5px; color: var(--ink-soft); margin-top: 2px; }
</style>
</head>
<body>

  <section class="card front">
    <div class="front-info">
      <div class="contact">
        <p class="person-name">Employee Name</p>
        <p class="person-role">Managing Director</p>
        <ul class="contact-list">
          <li>
            <span class="contact-icon">
              <svg width="10" height="12" viewBox="0 0 10 12"><rect x="1.5" y="0.5" width="7" height="11" rx="1.2" fill="none" stroke="#000" stroke-width="1.2"/><circle cx="5" cy="9.5" r=".8" fill="#000"/></svg>
            </span>123 456 7890
          </li>
          <li>
            <span class="contact-icon">
              <svg width="12" height="10" viewBox="0 0 12 10"><rect x=".6" y=".6" width="10.8" height="8.8" fill="none" stroke="#000" stroke-width="1.2"/><path d="M.6 .6 6 5.6 11.4 .6" fill="none" stroke="#000" stroke-width="1.2"/></svg>
            </span>you@yourmail.example
          </li>
        </ul>
      </div>
      <p class="brand-name">Grandline Limousine<br>&amp; Transportation</p>
    </div>
    <div class="photo-grid">
      <div class="photo-limo-exterior" role="img" aria-label="Photo of a black stretch limousine exterior"></div>
      <div class="photo-limo-interior" role="img" aria-label="Photo of a limousine interior with blue lighting"></div>
      <div class="photo-party-interior" role="img" aria-label="Photo of a party bus interior with pink seating"></div>
      <div class="photo-pink-limo" role="img" aria-label="Photo of a pink stretch limousine"></div>
      <div class="photo-suv" role="img" aria-label="Photo of a white SUV"></div>
    </div>
  </section>

  <section class="card back">
    <div class="back-vehicle" role="img" aria-label="Faint photo of a stretch limousine in the background"></div>
    <div class="back-content">
      <p class="brand-name">Grandline Limousine<br>&amp; Transportation</p>
      <div class="info-block">
        <p class="info-title">SERVICE</p>
        <p class="info-list">weddings | birthdays | proms | airport transportation</p>
      </div>
      <div class="info-block">
        <p class="info-title">SERVICE AREAS</p>
        <p class="info-list">houston | the woodlands | spring | tomball | cypress | kingwood</p>
      </div>
      <div class="info-block">
        <p class="info-title">VEHICLE TYPES</p>
        <p class="info-list">sedans | suvs | limos | party bus</p>
      </div>
    </div>
  </section>

</body>
</html>
```